PLW Gourmet Fungi web presence and site

The goal is to attract local buyers of fresh mushrooms and to both local and international buyers freeze dried mushrooms. Mushrooms grown will be oyster mushrooms (yellow, pink, blue, king), shiitake, lions main, chestnut, and more. My business will also be selling grow kits that help families who would like to grow there own mushrooms

Target Market(s)

Local restaurants, foodies and people seeking high quality fresh and freeze dried gourmet mushrooms

Font styles to use
Serif

Requirements
Must have
• Pictures of the various mushrooms grown along with the characteristics of each of the mushrooms. Recipes and cooking tips for the various mushrooms. There needs to be
1. Order forms with online payments
2. Feedback
3. Preorders for mushrooms that may be more seasonal
4.links to social media Gillbook, LinkedIn, etc... I am not knowledgeable in this area
5. Contact Us link email, address, phone
6. About Us link explaining Mark Oduya & Sonia Pettimore and a brief explanation about us and why we became Mushroom farmers
7. Descriptions of the various mushroom varieties grown and how they are best prepared and served
8. Why Freeze Drying mushrooms and the benefits of Freeze Drying over other methods of preservation.
Nice to have
• 1. Recipes and cooking tips for each of the mushrooms.
2. Weekly additional resources added to different pages
3. Q&A section
4. Food Blog with resources added weekly
5.

Flexibility with future expansion and growth is essential. I would like to have a growing site, not a stagnant site.
Should not have
• 1. Boring, bland presentation.
2. The web site is one to educate, promote the various mushrooms grown
3. No music, video or sound on the main pages but eventually a Vlog might be in the works.

I realize there is a lot of content requested but the content needs to attract buyers and to have the site a go to site for foodies

```html
<!DOCTYPE html>
<html lang="en">
<head>
<meta charset="utf-8">
<title>PLW Gourmet Fungi</title>
<link href="https://fonts.googleapis.com/css2?family=Montserrat:wght@400;500;600;700&family=Lato:wght@400;700&display=swap" rel="stylesheet">
<style>
:root{
  --green:#1f4a1d;
  --green-dark:#173a16;
  --ink:#1d1d1d;
  --muted:#6d6d6d;
  --line:#d8d8d8;
  --footer:#2a2a2a;
  --footer-text:#e6e6e6;
  --star:#f2b51a;
  --white:#ffffff;
}
*{box-sizing:border-box;margin:0;padding:0}
html,body{width:1200px;height:5329px;overflow:hidden}
body{font-family:"Lato",sans-serif;color:var(--ink);background:var(--white);position:relative}
h1,h2,h3,h4,.brand{font-family:"Montserrat",sans-serif}
a{color:inherit}
.section-title{font-size:36px;font-weight:600;text-align:center;color:var(--ink)}
.btn{display:inline-block;font-family:"Montserrat",sans-serif;font-weight:600;font-size:15px;text-decoration:none}
.btn-green{background:var(--green);color:#fff;padding:13px 28px}
.btn-white{background:#fff;color:var(--green);padding:12px 22px;font-size:14px}

/* header */
.site-header{position:absolute;top:0;left:0;width:1200px;height:78px;display:flex;align-items:center;padding:0 88px}
.brand{font-size:24px;font-weight:700;line-height:27px;width:220px}
.main-nav{display:flex;gap:34px;margin-left:190px;font-size:14px;color:#333}
.main-nav a{text-decoration:none}
.main-nav .active{border-bottom:1px solid #333}
.cart{margin-left:auto;font-size:14px;color:#333;display:flex;align-items:center;gap:10px}

/* hero */
.hero{position:absolute;top:78px;left:0;width:1200px;height:532px;background:radial-gradient(ellipse at 55% 55%,#e6b64a 0%,#c99a35 30%,#6f7a3c 65%,#3f4d2a 100%);text-align:center;color:#fff}
.hero h1{font-size:42px;font-weight:600;margin-top:163px;text-shadow:0 2px 6px rgba(0,0,0,.35)}
.hero p{font-size:17px;line-height:27px;width:760px;margin:14px auto 0;text-shadow:0 1px 4px rgba(0,0,0,.4)}
.hero .btn{margin-top:20px;padding:14px 28px;font-size:16px}

/* products */
.products{position:absolute;top:680px;left:0;width:1200px}
.carousel-arrow{position:absolute;font-size:22px;color:#555}
.product-cards{position:absolute;top:72px;left:88px;display:flex;gap:42px}
.product-card{width:310px;height:363px;background:#fff;box-shadow:0 2px 10px rgba(0,0,0,.15);padding:10px}
.product-photo{height:190px}
.product-card h3{font-size:20px;font-weight:500;margin-top:10px}
.product-card p{font-size:13px;line-height:23px;color:var(--muted);margin-top:6px}
.card-links{display:flex;justify-content:space-between;font-size:13px;color:var(--green);margin-top:6px}

/* about */
.about{position:absolute;top:1205px;left:0;width:1200px;height:525px;display:flex}
.about-photo{width:600px;height:100%;background:linear-gradient(135deg,#9fb2c2,#5e4634 55%,#3a2a20)}
.about-panel{width:600px;background:var(--green);color:#fff;padding:60px 90px 0 52px}
.about-panel h2{font-size:36px;font-weight:600}
.about-panel p{font-size:14px;line-height:28.5px;margin-top:18px;text-align:justify}
.about-panel .btn{margin-top:26px}

/* varieties */
.varieties{position:absolute;top:1805px;left:0;width:1200px}
.variety-list{display:flex;gap:24px;margin:26px 0 0 110px}
.variety{width:228px;text-align:center}
.variety-photo{width:228px;height:228px;border-radius:50%}
.variety h3{font-size:20px;font-weight:500;margin-top:18px}

/* freeze drying */
.freeze{position:absolute;top:2232px;left:0;width:1200px;height:525px;display:flex}
.freeze-panel{width:600px;background:var(--green);color:#fff;padding:60px 40px 0 90px}
.freeze-panel h2{font-size:38px;font-weight:600;line-height:44px}
.benefits{list-style:none;margin-top:22px}
.benefits li{font-size:14px;line-height:28.5px;padding-left:26px;position:relative}
.benefits li::before{content:"»";position:absolute;left:0;top:0}
.freeze-panel .btn{margin-top:22px}
.freeze-photo{width:600px;background:radial-gradient(circle at 45% 40%,#e9d9bf,#c7a37a 50%,#8a6a4b)}

/* feedback */
.feedback{position:absolute;top:2830px;left:0;width:1200px;text-align:center}
.stars{color:var(--star);font-size:16px;letter-spacing:6px;margin-top:12px}
.feedback p{font-size:16px;line-height:27px;color:var(--muted);width:940px;margin:14px auto 0}
.reviewers{display:flex;justify-content:center;align-items:center;gap:48px;margin-top:40px}
.avatar{border-radius:50%}
.avatar.small{width:92px;height:92px;background:linear-gradient(#d7c6c0,#b59a8f)}
.avatar.large{width:110px;height:110px;background:linear-gradient(#9a7a65,#4d3a2e)}
.arrow{font-size:28px;color:#444;margin:0 40px}
.reviewer-name{font-size:16px;color:var(--muted);margin-top:22px}

/* faq */
.faq{position:absolute;top:3247px;left:0;width:1200px;height:531px;background:linear-gradient(#2f4f2c,#27462a 60%,#2b4a2c);color:#fff;text-align:center}
.faq h2{font-size:36px;font-weight:600;margin-top:76px}
.faq-list{list-style:none;width:720px;margin:24px auto 0;text-align:left}
.faq-list li{font-size:15px;height:53px;line-height:50px;border-bottom:1px solid rgba(255,255,255,.35);display:flex;justify-content:space-between;padding:0 12px}
.faq-list li span:last-child{font-weight:700}
.faq .view-all{display:inline-block;font-size:13px;margin-top:22px}

/* blog */
.blog{position:absolute;top:3855px;left:0;width:1200px}
.blog-cards{position:absolute;top:70px;left:90px;display:flex;gap:16px}
.blog-card{width:332px;height:420px;border:1px solid var(--line);padding:6px;position:relative}
.blog-photo{height:200px;background:radial-gradient(circle at 50% 55%,#b58a45,#5a4a32 55%,#2f3033)}
.date-badge{position:absolute;top:166px;left:24px;width:64px;height:62px;background:var(--green);color:#fff;font-family:"Montserrat",sans-serif;font-size:19px;text-align:center;line-height:25px;padding-top:6px}
.blog-card h3{font-size:18px;font-weight:600;line-height:25px;margin:40px 16px 0}
.blog-card p{font-size:13px;line-height:22px;color:var(--muted);margin:12px 16px 0}
.read-more{display:block;font-family:"Montserrat",sans-serif;font-size:15px;font-weight:600;color:var(--green);margin:10px 16px 0;text-decoration:none}

/* order */
.order{position:absolute;top:4420px;left:0;width:1200px;text-align:center}
.order-form{display:grid;grid-template-columns:362px 362px;gap:20px 24px;width:748px;margin:30px auto 0}
.field{height:48px;border:1px solid #bdbdbd;font-size:14px;color:#444;text-align:left;padding:0 18px;line-height:46px;display:flex;justify-content:space-between}
.order .btn{margin-top:24px;font-weight:500;padding:12px 26px}

/* footer */
.site-footer{position:absolute;top:4833px;left:0;width:1200px;height:496px;background:var(--footer);color:var(--footer-text)}
.perks{display:flex;gap:0;padding:58px 0 0 90px}
.perk{display:flex;align-items:center;gap:18px;width:260px;font-size:13px;line-height:22px}
.perk-icon{width:56px;height:56px;border:2px solid #fff;border-radius:50%;display:flex;align-items:center;justify-content:center;flex:none}
.footer-cols{display:flex;padding:70px 0 0 88px}
.footer-cols h4{font-size:19px;font-weight:500;margin-bottom:18px}
.menu-grid{display:grid;grid-template-columns:152px 140px;gap:12px 0;font-size:10px;text-transform:uppercase}
.col-menu{width:320px}
.col-social{width:190px}
.social{display:flex;gap:10px;font-size:11px;align-items:center}
.col-contact{width:228px;font-size:10px;line-height:27px;text-transform:uppercase}
.col-news input{width:284px;height:42px;border:1px solid #888;background:transparent;color:#ddd;padding:0 16px;font-size:11px;font-family:"Lato",sans-serif}
.col-news .signup{width:284px;height:42px;background:var(--green);color:#fff;font-family:"Montserrat",sans-serif;font-weight:600;font-size:15px;text-align:center;line-height:42px;margin-top:12px}
.bottom-bar{position:absolute;left:88px;right:88px;top:448px;display:flex;justify-content:space-between;align-items:center;font-size:10px}
.pay{display:flex;gap:6px}
.pay span{background:#fff;color:#1f3a7a;font-size:8px;font-weight:700;padding:5px 6px;border-radius:2px}
</style>
</head>
<body>

<header class="site-header">
  <div class="brand">PLW Gourmet<br>Fungi</div>
  <nav class="main-nav">
    <a class="active" href="#">Home</a><a href="#">About Us</a><a href="#">Products</a><a href="#">Categories</a><a href="#">Blog</a><a href="#">Contact Us</a>
  </nav>
  <div class="cart">
    <svg width="16" height="14" viewBox="0 0 16 14"><path d="M0 1h3l2 8h8l2-6H4" fill="none" stroke="#333" stroke-width="1.8"/><circle cx="6" cy="12" r="1.4" fill="#333"/><circle cx="12" cy="12" r="1.4" fill="#333"/></svg>
    Add To Cart
  </div>
</header>

<section class="hero" role="img" aria-label="Photo of golden oyster mushrooms growing on a tree trunk">
  <h1>PLW Gourmet Fungi</h1>
  <p>Lorem ipsum dolor sit amet, consectetur adipiscing elit, sed do eiusmod tempor incididunt ut labore et dolore magna aliqua.</p>
  <a class="btn btn-green" href="#">Seasonal PreOrder</a>
</section>

<section class="products">
  <h2 class="section-title">Products</h2>
  <span class="carousel-arrow" style="left:40px;top:248px">‹</span>
  <span class="carousel-arrow" style="left:1150px;top:248px">›</span>
  <div class="product-cards">
    <article class="product-card">
      <div class="product-photo" role="img" aria-label="Oyster mushrooms on a wooden board" style="background:linear-gradient(135deg,#2b2b2b,#8a6a45 50%,#2a2a2a)"></div>
      <h3>Oyster Mushrooms</h3>
      <p>Lorem ipsum dolor sit amet, consectetur adipiscing elit, sed do eiusmod tempor incididunt ut labore et dolore</p>
      <div class="card-links"><a href="#">Recipes</a><a href="#">Cooking Tips</a></div>
    </article>
    <article class="product-card">
      <div class="product-photo" role="img" aria-label="Shiitake mushrooms in a bowl" style="background:radial-gradient(circle,#8a6440,#3a2d24 60%,#222)"></div>
      <h3>Shiitake</h3>
      <p>Lorem ipsum dolor sit amet, consectetur adipiscing elit, sed do eiusmod tempor incididunt ut labore et dolore</p>
      <div class="card-links"><a href="#">Recipes</a><a href="#">Cooking Tips</a></div>
    </article>
    <article class="product-card">
      <div class="product-photo" role="img" aria-label="Chestnut mushrooms in a pan" style="background:radial-gradient(circle,#7a3e22,#4a2a1c 60%,#2a1f1a)"></div>
      <h3>Chestnut</h3>
      <p>Lorem ipsum dolor sit amet, consectetur adipiscing elit, sed do eiusmod tempor incididunt ut labore et dolore</p>
      <div class="card-links"><a href="#">Recipes</a><a href="#">Cooking Tips</a></div>
    </article>
  </div>
</section>

<section class="about">
  <div class="about-photo" role="img" aria-label="Hands holding freshly picked chestnut mushrooms"></div>
  <div class="about-panel">
    <h2>About Us</h2>
    <p>Sed ut perspiciatis unde omnis iste natus error sit voluptatem accusantium doloremque laudantium, totam rem aperiam, eaque ipsa quae ab illo inventore veritatis et quasi architecto beatae vitae dicta sunt explicabo. Nemo enim ipsam voluptatem quia voluptas sit aspernatur aut odit aut fugit, sed quia consequuntur magni dolores eos qui ratione voluptatem sequi nesciunt. Neque porro quisquam est, qui dolorem ipsum quia dolor sit amet, consectetur, adipisci velit, sed quia non</p>
    <a class="btn btn-white" href="#">Meet Our Team</a>
  </div>
</section>

<section class="varieties">
  <h2 class="section-title">Varities Of Mushroom Gown</h2>
  <div class="variety-list">
    <div class="variety"><div class="variety-photo" role="img" aria-label="Oyster mushrooms close-up" style="background:radial-gradient(circle,#c9b6a6,#7a6658)"></div><h3>Oyster Mushrooms</h3></div>
    <div class="variety"><div class="variety-photo" role="img" aria-label="Shiitake mushrooms in a bowl" style="background:radial-gradient(circle,#8c6c4c,#3a2c22)"></div><h3>Shiitake</h3></div>
    <div class="variety"><div class="variety-photo" role="img" aria-label="Lion's mane mushroom" style="background:radial-gradient(circle,#f1ede4,#a89070)"></div><h3>Lions Main</h3></div>
    <div class="variety"><div class="variety-photo" role="img" aria-label="Chestnut mushrooms" style="background:radial-gradient(circle,#8a4a2a,#3a2418)"></div><h3>Chestnut</h3></div>
  </div>
</section>

<section class="freeze">
  <div class="freeze-panel">
    <h2>Why Freeze Drying<br>mushrooms</h2>
    <ul class="benefits">
      <li>Sed ut perspiciatis unde omnis iste natus error sit voluptatem accusantium doloremque laudantium</li>
      <li>Lorem ipsum dolor sit amet, consectetur adipiscing elit</li>
      <li>Excepteur sint occaecat cupidatat non proident</li>
      <li>Sed ut perspiciatis unde omnis iste natus error sit voluptatem accusantium doloremque laudantium</li>
      <li>Lorem ipsum dolor sit amet, consectetur adipiscing elit</li>
      <li>Excepteur sint occaecat cupidatat non proident</li>
    </ul>
    <a class="btn btn-white" href="#">Learn More</a>
  </div>
  <div class="freeze-photo" role="img" aria-label="Cluster of small pale mushrooms growing"></div>
</section>

<section class="feedback">
  <h2 class="section-title">Feedback From Customers</h2>
  <div class="stars">★★★★★</div>
  <p>Lorem ipsum dolor sit amet, consectetur adipiscing elit, sed do eiusmod tempor incididunt ut labore et dolore magna aliqua. Ut enim ad minim veniam, quis nostrud exerco laboris nisnsequat.</p>
  <div class="reviewers">
    <span class="arrow">⟵</span>
    <div class="avatar small" role="img" aria-label="Customer portrait"></div>
    <div class="avatar large" role="img" aria-label="Customer portrait"></div>
    <div class="avatar small" role="img" aria-label="Customer portrait"></div>
    <span class="arrow">⟶</span>
  </div>
  <div class="reviewer-name">Dana R., Oceanside, US</div>
</section>

<section class="faq" role="region" aria-label="Frequently asked questions over a dark green mushroom backdrop">
  <h2>FAQ</h2>
  <ul class="faq-list">
    <li><span>Lorem ipsum dolor sit amet, consectetur adipiscing elit, sed do eiusmod tempor</span><span>+</span></li>
    <li><span>Lorem ipsum dolor sit amet, consectetur adipiscing elit, sed do eiusmod tempor</span><span>+</span></li>
    <li><span>Lorem ipsum dolor sit amet, consectetur adipiscing elit, sed do eiusmod tempor</span><span>+</span></li>
    <li><span>Lorem ipsum dolor sit amet, consectetur adipiscing elit, sed do eiusmod tempor</span><span>+</span></li>
    <li><span>Lorem ipsum dolor sit amet, consectetur adipiscing elit, sed do eiusmod tempor</span><span>+</span></li>
  </ul>
  <a class="view-all" href="#">View All</a>
</section>

<section class="blog">
  <h2 class="section-title">Blog</h2>
  <span class="carousel-arrow" style="left:40px;top:255px;font-size:30px">‹</span>
  <span class="carousel-arrow" style="left:1148px;top:255px;font-size:30px">›</span>
  <div class="blog-cards">
    <article class="blog-card"><div class="blog-photo" role="img" aria-label="Sautéed mushrooms in a skillet"></div><div class="date-badge">25<br>FEB</div><h3>Lorem ipsum dolor sit amet, consectetur adipiscing</h3><p>Lorem ipsum dolor sit amet, consect etur adipiscing elit, sed do eiusmtempor incididunt ut labore et dolore</p><a class="read-more" href="#">Read More</a></article>
    <article class="blog-card"><div class="blog-photo" role="img" aria-label="Mushroom dish in a pan with cutlery"></div><div class="date-badge">25<br>FEB</div><h3>Lorem ipsum dolor sit amet, consectetur adipiscing</h3><p>Lorem ipsum dolor sit amet, consect etur adipiscing elit, sed do eiusmtempor incididunt ut labore et dolore</p><a class="read-more" href="#">Read More</a></article>
    <article class="blog-card"><div class="blog-photo" role="img" aria-label="Pan of roasted mushrooms"></div><div class="date-badge">25<br>FEB</div><h3>Lorem ipsum dolor sit amet, consectetur adipiscing</h3><p>Lorem ipsum dolor sit amet, consect etur adipiscing elit, sed do eiusmtempor incididunt ut labore et dolore</p><a class="read-more" href="#">Read More</a></article>
  </div>
</section>

<section class="order">
  <h2 class="section-title">Order Now</h2>
  <form class="order-form">
    <div class="field">Name</div>
    <div class="field">Phone No</div>
    <div class="field">Select Mushroom <span>⌄</span></div>
    <div class="field">Quantity <span>⌄</span></div>
    <div class="field">Address</div>
    <div class="field">Zip</div>
  </form>
  <a class="btn btn-green" href="#">Onlinepayment</a>
</section>

<footer class="site-footer">
  <div class="perks">
    <div class="perk"><div class="perk-icon"><svg width="26" height="26" viewBox="0 0 26 26"><path d="M5 13a8 8 0 0 1 14-5M21 13a8 8 0 0 1-14 5" fill="none" stroke="#fff" stroke-width="2.4"/><path d="M19 3v5h-5M7 23v-5h5" fill="none" stroke="#fff" stroke-width="2.4"/></svg></div><div>10 days return<br>3 days for free return</div></div>
    <div class="perk"><div class="perk-icon"><svg width="28" height="20" viewBox="0 0 28 20"><rect x="1" y="3" width="16" height="11" fill="#fff"/><path d="M17 6h6l4 4v4h-10z" fill="#fff"/><circle cx="7" cy="16" r="2.5" fill="#fff"/><circle cx="22" cy="16" r="2.5" fill="#fff"/></svg></div><div>Free Shipping<br>Free shipping on order</div></div>
    <div class="perk"><div class="perk-icon"><svg width="24" height="24" viewBox="0 0 24 24"><path d="M2 11 22 2 15 22l-3-8z" fill="#fff"/></svg></div><div>Proffesional Support<br>Call : +1 555 014 2277</div></div>
    <div class="perk"><div class="perk-icon"><svg width="24" height="24" viewBox="0 0 24 24"><rect x="3" y="9" width="18" height="13" fill="#fff"/><rect x="2" y="6" width="20" height="4" fill="#fff"/><rect x="11" y="6" width="2" height="16" fill="#2a2a2a"/></svg></div><div>Gift Card<br>Gift Card On Purchase</div></div>
  </div>
  <div class="footer-cols">
    <div class="col-menu"><h4>Main menu</h4>
      <div class="menu-grid"><span>Home</span><span>FAQ</span><span>About Us</span><span>Resources</span><span>Products</span><span>Shipping</span><span>Categories</span><span>International</span><span>Blog</span><span>Selling Grow Kits</span><span>Contact Us</span></div>
    </div>
    <div class="col-social"><h4>Stay In Touch</h4>
      <div class="social"><span>Gillbook</span><span>Capgram</span><span>Sporechat</span>
        <svg width="16" height="12" viewBox="0 0 16 12"><rect width="16" height="12" fill="#fff"/><path d="M0 0l8 6 8-6" fill="none" stroke="#2a2a2a" stroke-width="1.5"/></svg></div>
    </div>
    <div class="col-contact"><h4 style="text-transform:none;line-height:normal">Contact Us</h4>
      412 Fernbrook Rd #3 Millhaven,<br>OR 97099 USA<br>☎ +1 555 014 2277<br>✉ hello@plwfungi.example
    </div>
    <div class="col-news"><h4>News &amp; updates</h4>
      <input type="text" value="Enter Your Email address" aria-label="Email address">
      <div class="signup">Sign Up</div>
    </div>
  </div>
  <div class="bottom-bar">
    <span>© Copyrights 2020 The Company Name All Rights Reserved</span>
    <div class="pay"><span>Payline</span><span>Circlepay</span><span>Duopay</span><span>Bluecard</span></div>
  </div>
</footer>

</body>
</html>
```